Create a fantasy eBook cover for a Catholic Novel

I wrote a novel called Blue Lantern Tuesday, The central event occurs when a priest drops a communion wafer on a lady's red sneaker.
I need the the image to show a communion wafer on top of the sneaker.
The sneaker is magical in that it is flashing so any effect you can apply that would communicate that electric activity emanating from the sneaker would be helpful.

The complete book title is:

Blue Lantern Tuesday
by Paul Dovetti

Ideal dimensions for cover files are 2,560 pixels in height x 1,600 pixels in width. image should be 2500 pixels in height. Minimum dimensions of 1000 pixels in height and 625 pixels in width.

```html
<!DOCTYPE html>
<html lang="en">
<head>
<meta charset="utf-8">
<title>Blue Lantern Tuesday — Paul Dovetti</title>
<link rel="stylesheet" href="https://fonts.googleapis.com/css2?family=Cinzel:wght@700;900&display=swap">
<style>
  :root {
    --page-bg: #ececec;
    --cover-deep: #2a0303;
    --cover-mid: #6e0a06;
    --cover-glow: #b3200c;
    --cream: #f6f2d6;
    --gold-light: #f4cf4a;
    --gold-mid: #e0a52c;
    --gold-dark: #b8641e;
    --flare-core: #ffd27a;
    --flare: #ff6a1e;
    --spark: #ff8a3a;
    --sneaker-red: #d3162a;
    --wafer: #e6d196;
  }
  * { margin: 0; padding: 0; box-sizing: border-box; }
  html, body {
    width: 1200px;
    height: 2482px;
    overflow: hidden;
    background: var(--page-bg);
  }
  .book-cover {
    position: absolute;
    left: 50px;
    top: 361px;
    width: 1100px;
    height: 1760px;
    overflow: hidden;
    background:
      radial-gradient(ellipse 60% 45% at 50% 62%, var(--cover-glow) 0%, var(--cover-mid) 45%, transparent 80%),
      radial-gradient(ellipse 90% 70% at 50% 35%, var(--cover-mid) 0%, var(--cover-deep) 85%);
    box-shadow: 18px 22px 26px rgba(0, 0, 0, 0.35);
  }
  .cover-title {
    position: absolute;
    left: 0;
    top: 0;
    width: 1100px;
    height: 700px;
    font-family: "Cinzel", "Trajan Pro", serif;
    font-weight: 900;
  }
  .cover-title .title-cream { fill: var(--cream); }
  .cover-art {
    position: absolute;
    left: 30px;
    top: 700px;
    width: 1040px;
    height: 900px;
    background:
      radial-gradient(circle 62px at 50% 10%, var(--wafer) 0%, #d2b46a 90%, transparent 100%),
      radial-gradient(ellipse 34% 30% at 62% 50%, var(--sneaker-red) 0%, rgba(211, 22, 42, 0.75) 55%, transparent 90%),
      radial-gradient(ellipse 30% 20% at 36% 70%, var(--sneaker-red) 0%, rgba(211, 22, 42, 0.7) 55%, transparent 90%),
      radial-gradient(ellipse 22% 20% at 45% 55%, var(--flare-core) 0%, var(--flare) 45%, transparent 100%),
      radial-gradient(ellipse 55% 50% at 50% 55%, rgba(255, 106, 30, 0.75) 0%, rgba(255, 138, 58, 0.35) 50%, transparent 80%),
      radial-gradient(ellipse 70% 60% at 50% 55%, rgba(255, 90, 26, 0.3) 0%, transparent 85%);
  }
  .cover-author {
    position: absolute;
    left: 0;
    top: 1620px;
    width: 1100px;
    height: 90px;
    font-family: "Cinzel", "Trajan Pro", serif;
    font-weight: 700;
  }
  .cover-author text { fill: var(--cream); }
</style>
</head>
<body>
  <main class="book-cover">
    <svg class="cover-title" viewBox="0 0 1100 700" aria-label="Blue Lantern Tuesday">
      <defs>
        <linearGradient id="gold-title" x1="0" y1="0" x2="1" y2="0">
          <stop offset="0" stop-color="var(--gold-dark)"/>
          <stop offset="0.3" stop-color="var(--gold-light)"/>
          <stop offset="0.55" stop-color="var(--gold-mid)"/>
          <stop offset="0.8" stop-color="var(--gold-light)"/>
          <stop offset="1" stop-color="var(--gold-dark)"/>
        </linearGradient>
      </defs>
      <text class="title-cream" x="550" y="352" font-size="350" text-anchor="middle"
            textLength="730" lengthAdjust="spacingAndGlyphs">BLUE</text>
      <text x="550" y="509" font-size="168" text-anchor="middle" fill="url(#gold-title)"
            textLength="920" lengthAdjust="spacingAndGlyphs">LANTERN</text>
      <text class="title-cream" x="550" y="662" font-size="170" text-anchor="middle"
            textLength="736" lengthAdjust="spacingAndGlyphs">TUESDAY</text>
    </svg>

    <div class="cover-art" role="img"
         aria-label="A communion wafer resting on a pair of flashing red sneakers, with bright orange electric lightning bursting out in all directions"></div>

    <svg class="cover-author" viewBox="0 0 1100 90" aria-label="Paul Dovetti">
      <text x="550" y="64" font-size="68" text-anchor="middle"
            textLength="779" lengthAdjust="spacing">PAUL DOVETTI</text>
    </svg>
  </main>
</body>
</html>
```